Logo + Label Design (Men’s Grooming Brand & Product Packaging)

Design a logo and 2 oz pomade label for Brel, a modern men’s grooming brand focused on clean, high-quality, natural ingredients. The design should establish a bold, masculine, minimalist identity that can later extend to products like shaving gel and body wash.

Key Requirements

Create a primary logo for “Brel” and a core label for the 2 oz pomade jar (screw-top).

Use a clean, modern style — masculine, confident, and approachable (think Dorran’s, Velta, Northfield Kit).

Design for 1–2 color screen printing on solid jar colors (white, black, or navy).

Avoid gradients, foil, or embossing. Must work in black & white.

Provide: vector logo, mockup of the 2 oz jar, color palette (CMYK/RGB/HEX), and font specs.

Winning design may lead to future projects (body wash, shave gel, skincare lines).

Font styles to use
Other font styles liked:
• We like the fonts and design concept in the attached mockup.

Requirements
Should not have
• We want to avoid too much writing or busy designs. We want to avoid having graphics/illustrations embedded in the logo if they will cause the brand to look less classy or sophisticated. We also want the design to look simple and all-American (e.g. Hollister and Vane, Pine Ledger, The KIM, etc). We’d like to give a Pellham & Royce vibe that feels classy and high end.

```html
<!DOCTYPE html>
<html lang="en">
<head>
<meta charset="utf-8">
<title>Brel Hair Pomade Label</title>
<link href="https://fonts.googleapis.com/css2?family=Poppins:wght@400;500;600;700&display=swap" rel="stylesheet">
<style>
  :root {
    --backdrop: #e2e2e2;
    --label-black: #050505;
    --ink-white: #ffffff;
  }
  * { margin: 0; padding: 0; box-sizing: border-box; }
  html, body { width: 1200px; height: 1200px; overflow: hidden; }
  body {
    background: var(--backdrop);
    font-family: "Poppins", sans-serif;
    color: var(--ink-white);
    position: relative;
  }
  .label {
    position: absolute;
    background: var(--label-black);
    box-shadow: 0 3px 8px rgba(0,0,0,0.25);
  }
  .label--wrap { left: 30px; top: 500px; width: 909px; height: 200px; }
  .label--lid { left: 970px; top: 500px; width: 200px; height: 200px; }

  .maker, .site {
    position: absolute;
    top: 100px;
    transform: translate(-50%, -50%) rotate(-90deg);
    white-space: nowrap;
    font-size: 9.6px; line-height: 1.4;
  }
  .maker { left: 48px; }
  .site { left: 110px; }
  .maker strong, .site strong { font-weight: 700; display: block; }

  .claims {
    position: absolute;
    left: 160px; top: 46px; width: 166px; height: 110px;
    border: 1px solid var(--ink-white);
    border-radius: 7px;
    padding: 7px 6px 0 8px;
    list-style: none;
    font-size: 11px; line-height: 1.15;
  }
  .claims li { position: relative; padding-left: 11px; margin-bottom: 5px; white-space: nowrap; }
  .claims li:last-child { margin-bottom: 0; }
  .claims li::before {
    content: ""; position: absolute; left: 0; top: 4.5px;
    width: 4.5px; height: 4.5px; border-radius: 50%; background: var(--ink-white);
  }

  .front {
    position: absolute; text-align: center;
    display: flex; flex-direction: column; align-items: center;
  }
  .label--wrap .front { left: 344px; top: 26px; width: 220px; }
  .label--lid .front { left: 0; top: 36px; width: 200px; }
  .brand { font-weight: 700; letter-spacing: 0.5px; line-height: 1; }
  .label--wrap .brand { font-size: 44px; margin-bottom: 8px; }
  .label--lid .brand { font-size: 36px; margin-bottom: 6px; }
  .product-tag {
    background: var(--ink-white); color: var(--label-black);
    border-radius: 4px; font-weight: 500; line-height: 1.1;
  }
  .label--wrap .product-tag { font-size: 15px; padding: 2px 7px; }
  .label--lid .product-tag { font-size: 12.5px; padding: 1px 6px; }
  .scent, .hold { font-weight: 400; line-height: 1.15; }
  .label--wrap .scent { font-size: 15px; margin-top: 2px; }
  .label--lid .scent { font-size: 12.5px; }
  .label--wrap .hold { font-size: 14px; }
  .label--lid .hold { font-size: 11px; margin-top: 8px; }
  .weight { font-size: 10px; line-height: 1.2; }
  .label--wrap .weight { margin-top: 4px; }
  .label--lid .weight { margin-top: 10px; font-size: 10.5px; }

  .fine-print {
    position: absolute;
    left: 583px; top: 30px; width: 296px;
    font-size: 10px; line-height: 1.35;
    text-align: justify;
  }
  .fine-print p + p { margin-top: 14px; }
  .fine-print strong { font-weight: 700; }
</style>
</head>
<body>
  <section class="label label--wrap" aria-label="Jar wrap label">
    <div class="maker">
      <strong>MANUFACTURED BY:</strong>
      Brel Grooming Co.,<br>Ashford, NC 27514
    </div>
    <div class="site">
      <strong>Visit us at</strong>
      brelgrooming.com
    </div>

    <ul class="claims">
      <li>Naturally derived plant</li>
      <li>Bee-based ingredients</li>
      <li>Alcohol Free</li>
      <li>Non-Irritating</li>
      <li>Formulated to minimize<br>scalp irritation</li>
    </ul>

    <div class="front">
      <div class="brand">Brel</div>
      <div class="product-tag">Hair Pomade</div>
      <div class="scent">Fresh &amp; Clean</div>
      <div class="hold">Medium Hold - Matte Finish</div>
      <div class="weight">NET WT<br>2 oz / 57 g</div>
    </div>

    <div class="fine-print">
      <p><strong>DIRECTIONS:</strong> Melt small amount of pomade between hands before massaging into damp hair (for sleeker look) or dry hair (for more texture). Style as desired. For external use only. Avoid contact with eyes. If irritation occurs, discontinue use.</p>
      <p><strong>INGREDIENTS:</strong> Butyrospermum Parkii (Shea Butter), Cera Alba (Beeswax), Polyglycerol-3 Beeswax (Cera Bellina), Caprylic/Capric Triglyceride (Fractionated Coconut Oil), Tocopherol (Vitamin E), Fragrance (Parfum)</p>
    </div>
  </section>

  <section class="label label--lid" aria-label="Jar lid label">
    <div class="front">
      <div class="brand">Brel</div>
      <div class="product-tag">Hair Pomade</div>
      <div class="scent">Fresh &amp; Clean</div>
      <div class="hold">Medium Hold - Matte Finish</div>
      <div class="weight">NET WT<br>2 oz / 57 g</div>
    </div>
  </section>
</body>
</html>
```